CareStatute Chambers Mailer for Small Medical Offices and Solo Physician Practices

CareStatute Chambers -- We are a local health law firm looking to provide advice to medical practices on the legal issues they face. We strive to function as a general counsel for medical practices and provide tailored solutions to meet the needs of our clients. Please see postcard content ideas in document attached. Our firm colors are royal blue, gray and white and black.

Target Market(s)

Small medical offices, solo physician practices in the Southeast Michigan (Detroit Metro area)

Industry/Entity Type

Law Firm

Font styles to use
Sans Serif

Colors
0991cd
3176b5
ffffff
7f7f7f
1b1b1b

Requirements
Must have
• Brief summary of legal services offered, bullet pointed list of practice areas/issues
• Contact information, website, address
• Pictures of attorneys
• Prefer the use of our firm's colors (royal blue, gray, white, black)
Nice to have
• Included some purchased stock images that could also be incorporated

```html
<!DOCTYPE html>
<html lang="en">
<head>
<meta charset="utf-8">
<title>CareStatute Chambers – Health Law Mailer</title>
<link rel="stylesheet" href="https://fonts.googleapis.com/css2?family=Jost:wght@600;700&family=Open+Sans:wght@300;400;600;700&family=Oswald:wght@500;600&display=swap">
<style>
  :root {
    --royal: #0a63b3;
    --sky: #1aa9e8;
    --link: #0991cd;
    --gray: #5f6062;
    --ink: #1b1b1b;
    --text-soft: #333333;
    --white: #ffffff;
    --stage: #1f1f1f;
    --photo-light: #4d6a96;
    --photo-dark: #223f72;
  }
  * { margin: 0; padding: 0; box-sizing: border-box; }
  html, body { width: 1200px; height: 727px; overflow: hidden; background: var(--stage); }
  body { font-family: "Open Sans", Arial, sans-serif; }

  .mailer {
    position: absolute; left: 92px; top: 87px;
    width: 1016px; height: 553px; background: var(--white);
  }
  .headline {
    position: absolute; left: 0; right: 0; top: 28px;
    text-align: center; color: var(--royal);
    font-family: "Jost", "Century Gothic", sans-serif; font-weight: 600;
    font-size: 61px; letter-spacing: 0.5px; line-height: 1;
  }
  .hero-photo {
    position: absolute; left: 0; top: 102px; width: 557px; height: 308px;
    background: linear-gradient(160deg, var(--photo-light) 0%, var(--photo-dark) 100%);
  }
  .services-panel {
    position: absolute; left: 557px; top: 102px; width: 459px; height: 331px;
    background: var(--royal); color: var(--white);
  }
  .services-intro {
    position: absolute; left: 29px; top: 23px; width: 400px;
    font-weight: 300; font-size: 15.2px; line-height: 20px;
  }
  .services-list {
    position: absolute; left: 28px; top: 99px; list-style: none;
    font-weight: 700; font-size: 14.4px; line-height: 20.6px;
  }
  .services-list li { display: flex; align-items: center; gap: 9px; }
  .services-list svg { width: 10px; height: 8px; flex: none; }
  .consult-badge {
    position: absolute; left: 298px; top: 106px; width: 148px; height: 148px;
    border-radius: 50%; background: var(--sky); color: var(--white);
    font-family: "Oswald", "Arial Narrow", sans-serif; text-align: center;
    display: flex; flex-direction: column; align-items: center; justify-content: center;
  }
  .consult-badge .badge-big { font-size: 46px; font-weight: 600; line-height: 44px; letter-spacing: 1px; }
  .consult-badge .badge-small { font-size: 18.5px; font-weight: 500; line-height: 23px; }

  .firm-name {
    position: absolute; left: 103px; top: 462px;
    display: flex; align-items: center; gap: 12px;
    font-weight: 600; font-size: 30px; color: var(--gray); letter-spacing: -0.3px;
  }
  .firm-name .mark { width: 20px; height: 20px; background: var(--royal); }

  .contact {
    position: absolute; left: 552px; top: 449px; width: 450px; color: var(--ink);
    font-size: 13.5px; font-style: normal;
  }
  .contact-firm { font-weight: 600; font-size: 14px; margin-bottom: 7px; padding-left: 4px; }
  .contact-row { display: flex; }
  .contact-address {
    width: 253px; position: relative; padding-left: 21px; line-height: 17px;
    color: var(--text-soft); white-space: nowrap;
  }
  .contact-address svg { position: absolute; left: 0; top: 2px; }
  .contact-direct { line-height: 19px; margin-top: -2px; white-space: nowrap; }
  .contact-direct div { display: flex; align-items: center; gap: 7px; }
  .contact-phone { font-weight: 700; font-size: 14.5px; }
  .contact-email { color: var(--text-soft); }
  .contact-web { margin-top: 3px; color: var(--link); font-weight: 700; font-size: 16px; padding-left: 20px; white-space: nowrap; }
</style>
</head>
<body>
<main class="mailer">
  <h1 class="headline">HEALTH LAW QUESTIONS?</h1>

  <div class="hero-photo" role="img" aria-label="Stock photo of a stethoscope and a judge's gavel on a blue leather folder"></div>

  <section class="services-panel">
    <p class="services-intro">We are local, experienced health lawyers available to provide efficient, effective advice on the issues impacting your healthcare business every day, including:</p>
    <ul class="services-list">
      <li><svg viewBox="0 0 10 8"><path d="M1 4l3 3 5-6" fill="none" stroke="#1aa9e8" stroke-width="2"/></svg>Contract review and negotiation</li>
      <li><svg viewBox="0 0 10 8"><path d="M1 4l3 3 5-6" fill="none" stroke="#1aa9e8" stroke-width="2"/></svg>Stark and Anti-kickback matters</li>
      <li><svg viewBox="0 0 10 8"><path d="M1 4l3 3 5-6" fill="none" stroke="#1aa9e8" stroke-width="2"/></svg>Reimbursement and payer issues</li>
      <li><svg viewBox="0 0 10 8"><path d="M1 4l3 3 5-6" fill="none" stroke="#1aa9e8" stroke-width="2"/></svg>HIPAA</li>
      <li><svg viewBox="0 0 10 8"><path d="M1 4l3 3 5-6" fill="none" stroke="#1aa9e8" stroke-width="2"/></svg>Vendor issues</li>
      <li><svg viewBox="0 0 10 8"><path d="M1 4l3 3 5-6" fill="none" stroke="#1aa9e8" stroke-width="2"/></svg>Licensing matters</li>
      <li><svg viewBox="0 0 10 8"><path d="M1 4l3 3 5-6" fill="none" stroke="#1aa9e8" stroke-width="2"/></svg>Employee issues</li>
      <li><svg viewBox="0 0 10 8"><path d="M1 4l3 3 5-6" fill="none" stroke="#1aa9e8" stroke-width="2"/></svg>Difficult patient matters</li>
      <li><svg viewBox="0 0 10 8"><path d="M1 4l3 3 5-6" fill="none" stroke="#1aa9e8" stroke-width="2"/></svg>Subpoenas and medical record requests</li>
      <li><svg viewBox="0 0 10 8"><path d="M1 4l3 3 5-6" fill="none" stroke="#1aa9e8" stroke-width="2"/></svg>Leases and landlord-tenant issues</li>
    </ul>
    <div class="consult-badge">
      <span class="badge-big">FREE</span>
      <span class="badge-small">CONSULTATIONS</span>
      <span class="badge-small">AVAILABLE</span>
    </div>
  </section>

  <div class="firm-name"><span>CareStatute Chambers</span><span class="mark"></span></div>

  <address class="contact">
    <div class="contact-firm">CareStatute Chambers</div>
    <div class="contact-row">
      <div class="contact-address">
        <svg width="13" height="13" viewBox="0 0 13 13"><circle cx="6.5" cy="6.5" r="6.5" fill="#1aa9e8"/><path d="M6.5 2.8a2.4 2.4 0 0 0-2.4 2.4c0 1.8 2.4 4.6 2.4 4.6s2.4-2.8 2.4-4.6a2.4 2.4 0 0 0-2.4-2.4z" fill="#fff"/><circle cx="6.5" cy="5.2" r="0.9" fill="#1aa9e8"/></svg>
        18400 Meridian Ave, Suite 310<br>Northgate, MI 48190
      </div>
      <div class="contact-direct">
        <div class="contact-phone"><svg width="13" height="13" viewBox="0 0 13 13"><circle cx="6.5" cy="6.5" r="6.5" fill="#1aa9e8"/><path d="M4.3 3.4l1.2 1.4-.6.9c.4.9 1.1 1.6 2 2l.9-.6 1.4 1.2-.8 1c-2.4-.3-4.6-2.5-4.9-4.9z" fill="#fff"/></svg>248.555.0163</div>
        <div class="contact-email"><svg width="13" height="13" viewBox="0 0 13 13"><circle cx="6.5" cy="6.5" r="6.5" fill="#1aa9e8"/><rect x="3.5" y="4.3" width="6" height="4.4" fill="none" stroke="#fff" stroke-width="1"/><path d="M3.5 4.5l3 2.3 3-2.3" fill="none" stroke="#fff" stroke-width="1"/></svg>info@carestatutechambers.com</div>
      </div>
    </div>
    <div class="contact-web">www.carestatutechambers.com</div>
  </address>
</main>
</body>
</html>
```